BOLD & MINIMALIST DESIGN NEEDED

We want a very bold but minimalistic business card design that is impactful and utilizes both sides of the business card. Our current logo is included for your use.

We want bold fonts and good use of negative space. We don't want the logo to overpower the design.

Target Market(s)

Professionals who are building new commercial buildings.

Industry/Entity Type

Construction

Contact Information for Business Card

Name, Title, email, office phone, cell phone, website

Font styles to use
Serif
Sans Serif

Requirements
Must have
• Bold design!

```html
<!DOCTYPE html>
<html lang="en">
<head>
<meta charset="utf-8">
<title>Ridgeline Design + Build – Business Card</title>
<link rel="stylesheet" href="https://fonts.googleapis.com/css2?family=Montserrat:wght@400;500&family=Oswald:wght@500;600&display=swap">
<style>
  :root {
    --backdrop: #d8d0c6;
    --card-frost: #eceeec;
    --card-dark: #1f1d1c;
    --brand-green: #6cc51f;
    --brand-green-deep: #4f9a12;
    --ink: #1c1c1c;
    --contact-text: #d9d6d2;
    --title-text: #e4e2df;
  }
  * { margin: 0; padding: 0; box-sizing: border-box; }
  html, body {
    width: 1200px;
    height: 887px;
    overflow: hidden;
    background: var(--backdrop);
  }
  .canvas {
    position: relative;
    width: 1200px;
    height: 887px;
  }
  .business-card {
    position: absolute;
    left: 100px;
    top: 183px;
    width: 1000px;
    height: 520px;
    border-radius: 28px;
    overflow: hidden;
    background: var(--card-frost);
    box-shadow: 0 18px 40px rgba(0,0,0,0.18);
  }
  .card-shapes {
    position: absolute;
    inset: 0;
  }
  .brand-lockup {
    position: absolute;
    top: 120px;
    left: 0;
    right: 0;
    display: flex;
    align-items: center;
    justify-content: center;
    gap: 16px;
  }
  .brand-square {
    width: 34px;
    height: 34px;
    background: var(--brand-green);
  }
  .brand-name {
    font-family: "Oswald", sans-serif;
    font-weight: 600;
    font-size: 46px;
    letter-spacing: 2px;
    color: var(--ink);
    text-transform: uppercase;
  }
  .contact-list {
    position: absolute;
    left: 58px;
    top: 378px;
    list-style: none;
    font-family: "Montserrat", sans-serif;
    font-weight: 400;
    font-size: 21px;
    color: var(--contact-text);
  }
  .contact-list li {
    display: flex;
    align-items: center;
    gap: 10px;
    height: 29px;
  }
  .contact-icon {
    width: 20px;
    height: 20px;
    flex: none;
  }
  .contact-list .accent { color: var(--brand-green); }
  .person {
    position: absolute;
    right: 56px;
    top: 388px;
    text-align: right;
  }
  .person-name {
    font-family: "Oswald", sans-serif;
    font-weight: 500;
    font-size: 48px;
    line-height: 1;
    color: var(--brand-green);
    text-transform: uppercase;
  }
  .person-title {
    margin-top: 8px;
    font-family: "Montserrat", sans-serif;
    font-weight: 400;
    font-size: 21px;
    letter-spacing: 1px;
    color: var(--title-text);
    text-transform: uppercase;
  }
</style>
</head>
<body>
<main class="canvas">
  <section class="business-card">
    <svg class="card-shapes" viewBox="0 0 1000 520" width="1000" height="520" aria-hidden="true">
      <defs>
        <linearGradient id="greenSweep" x1="0" x2="1" y1="0" y2="0">
          <stop offset="0" stop-color="var(--brand-green-deep)"/>
          <stop offset="0.5" stop-color="var(--brand-green)"/>
          <stop offset="1" stop-color="var(--brand-green-deep)"/>
        </linearGradient>
      </defs>
      <path d="M0,340 Q500,240 1000,340 Q500,256 0,340 Z" fill="url(#greenSweep)"/>
      <path d="M0,350 Q500,262 1000,350 L1000,520 L0,520 Z" fill="var(--card-dark)"/>
    </svg>

    <div class="brand-lockup">
      <span class="brand-square"></span>
      <span class="brand-name">Ridgeline Design + Build</span>
    </div>

    <ul class="contact-list">
      <li>
        <svg class="contact-icon" viewBox="0 0 20 20" aria-hidden="true"><path d="M5 2 L8 2 L9 6 L7 8 Q9 12 12 13 L14 11 L18 12 L18 15 Q17 18 14 18 Q4 16 2 6 Q2 3 5 2 Z" fill="var(--brand-green)"/></svg>
        <span>(555) 214-7730</span>
      </li>
      <li>
        <svg class="contact-icon" viewBox="0 0 20 20" aria-hidden="true"><path d="M2 7 Q10 1 18 7 L16 9 L13 8 L13 6 Q10 5 7 6 L7 8 L4 9 Z" fill="var(--brand-green)"/><rect x="4" y="10" width="12" height="8" rx="2" fill="var(--brand-green)"/></svg>
        <span>(555) 214-7730</span>
      </li>
      <li>
        <svg class="contact-icon" viewBox="0 0 20 20" aria-hidden="true"><rect x="2" y="5" width="16" height="11" fill="none" stroke="var(--brand-green)" stroke-width="1.8"/><path d="M2 5 L10 11 L18 5" fill="none" stroke="var(--brand-green)" stroke-width="1.8"/></svg>
        <span><span class="accent">ridgeline</span>design@mail.com</span>
      </li>
      <li>
        <svg class="contact-icon" viewBox="0 0 20 20" aria-hidden="true"><circle cx="10" cy="10" r="8" fill="none" stroke="var(--brand-green)" stroke-width="1.6"/><ellipse cx="10" cy="10" rx="3.5" ry="8" fill="none" stroke="var(--brand-green)" stroke-width="1.4"/><path d="M2 10 H18 M4 6 H16 M4 14 H16" stroke="var(--brand-green)" stroke-width="1.2"/></svg>
        <span>www.<span class="accent">ridgeline</span>design.com</span>
      </li>
    </ul>

    <div class="person">
      <p class="person-name">Marcus Whitfield</p>
      <p class="person-title">Owner</p>
    </div>
  </section>
</main>
</body>
</html>
```